PDF flyer for our companies' two main products: Food processing machines.

PDF flyer with showcasing two products. Flyer can be one page per product, or both products on the same page.

Product #1: Labeled "Ribbon blenders".
Showing a photo of the machine, and the details/features offered with that machine. Product description must also say: "Sizes available; 2 Cu Ft. - 450 Cu Ft."

Product #2: Labeled: " Auger hoppers / Screw feeders"
Showing a photo of the machine, and the details/features offered with that machine.

SEE UPLOADED IMAGES; "Ribbon Blenders EXAMPLE FLYER".
& "Auger Hoppers / Screw Conveyors EXAMPLE FLYER" for a rough idea of what we are looking for.

Target Market(s)

Copackers, Packing houses, Food manufacturers, protein powder producers,

Industry/Entity Type

Commercial Food processing / packing / mixing equipment

Font styles to use
Serif

Colors
0054AA
0677BA
7BADD7
CADEEF
E8F1F8

Requirements
Must have
• Company logo on top of flyer.
Nice to have
• I would like for the flyer to show some stock images of common ingredients, similar to the images uploaded.
Should not have
• Pictures with background. Backgrounds must be removed from provides photos. "clipping path"

```html
<!DOCTYPE html>
<html lang="en">
<head>
<meta charset="utf-8">
<title>Steelgate Equipment – Product Flyers</title>
<link href="https://fonts.googleapis.com/css2?family=Montserrat:wght@300;400;500;700&display=swap" rel="stylesheet">
<style>
:root{
  --ink:#111;
  --black:#000;
  --brand-deep:#0a45a0;
  --brand:#0054aa;
  --brand-mid:#0677ba;
  --brand-soft:#7badd7;
  --brand-pale:#cadeef;
  --brand-mist:#e8f1f8;
  --stage:#bfe1f6;
  --white:#fff;
}
*{box-sizing:border-box;margin:0;padding:0}
html,body{width:1200px;height:863px;overflow:hidden}
body{background:var(--stage);font-family:"Montserrat",sans-serif;color:var(--ink);position:relative}
.page{position:absolute;top:60px;width:526px;height:743px;background:var(--white);overflow:hidden}
.page--auger{left:66px}
.page--ribbon{left:608px}
.masthead{position:absolute;left:0;top:0;width:526px;height:140px}
.brand{position:absolute;left:0;top:30px;width:526px;text-align:center;color:var(--white);font-weight:500;font-size:22px;letter-spacing:3px;text-transform:uppercase}
.title{position:absolute;left:0;width:526px;text-align:center;color:var(--brand-deep);font-weight:400;line-height:1.2}
.page--auger .title{top:142px;font-size:32px;line-height:38px}
.page--ribbon .title{top:140px;font-size:31px}
.sizes{position:absolute;left:0;top:181px;width:526px;text-align:center;font-size:11px;font-weight:400}
.section-head{position:absolute;color:var(--brand);font-weight:700;text-transform:uppercase}
.ticks{position:absolute;list-style:none;font-weight:300}
.ticks li{position:relative}
.ticks li::before{content:"";position:absolute;left:0;width:4px;height:7px;border:solid var(--brand);border-width:0 2px 2px 0;transform:rotate(45deg)}
.ticks li.plain::before{display:none}
.page--auger .section-head{top:244px;font-size:13px}
.page--auger .ticks{top:276px;font-size:9.2px;line-height:16.2px}
.page--auger .ticks li{padding-left:21px}
.page--auger .ticks li::before{top:3px;left:3px}
.page--ribbon .section-head{top:236px;font-size:10px}
.page--ribbon .ticks{top:258px;font-size:6.6px;line-height:11.6px}
.page--ribbon .ticks li{padding-left:15px}
.page--ribbon .ticks li::before{top:2px;left:2px;width:3px;height:6px;border-width:0 1.5px 1.5px 0}
.photo{position:absolute}
.spec{position:absolute;border-collapse:collapse;background:var(--white);color:var(--ink)}
.spec td{border:1px solid var(--ink);white-space:nowrap;padding:0 1.5px}
.spec--auger{left:274px;top:521px;width:244px;font-size:5.6px;line-height:7.1px;font-weight:500;border:1.5px solid var(--ink)}
.spec--auger td.c{text-align:center}
.spec--ribbon{left:288px;top:472px;width:230px;font-size:3.6px;line-height:5.1px;font-weight:500}
.spec--ribbon td{border-width:0.6px}
.spec--ribbon tr:first-child td,.spec--ribbon td:first-child{font-weight:700}
</style>
</head>
<body>

<section class="page page--auger">
  <svg class="masthead" viewBox="0 0 526 140" aria-hidden="true">
    <path d="M0 0H526V98Q330 128 0 46Z" fill="var(--black)"/>
    <path d="M0 46Q330 128 526 98V113Q330 142 0 68Z" fill="var(--brand-deep)"/>
  </svg>
  <div class="brand">Steelgate Equipment</div>

  <h1 class="title">AUGER HOPPERS / SCREW<br>FEEDERS</h1>

  <h2 class="section-head" style="left:51px">Standard Features</h2>
  <ul class="ticks" style="left:51px">
    <li>Direct Drive.</li>
    <li>304 Stainless steel construction</li>
    <li>Stainless steel safety grating.</li>
    <li>Pre-wired control panel</li>
    <li>Electric Vibrator.</li>
    <li>Castor Wheels.</li>
  </ul>

  <h2 class="section-head" style="left:282px">Options</h2>
  <ul class="ticks" style="left:282px">
    <li>Square or round hopper. 3.5cf and</li>
    <li class="plain">7cf hoppers are standard.</li>
    <li>Custom hoppers up to 200cf.</li>
    <li>VFD (Variable Frequency Drive).</li>
    <li>Clamshell Auger tube for easy cleanout.</li>
    <li class="plain">316 Stainless steel construction.</li>
  </ul>

  <svg class="photo" style="left:0;top:370px" width="526" height="373" role="img" aria-label="Floor and wall backdrop behind the machines">
    <defs><linearGradient id="floor" x1="0" y1="0" x2="0" y2="1">
      <stop offset="0" stop-color="#fff"/><stop offset=".55" stop-color="#eef0f2"/><stop offset=".8" stop-color="#5b5d60"/><stop offset="1" stop-color="#3d3e40"/>
    </linearGradient></defs>
    <rect width="526" height="373" fill="url(#floor)"/>
  </svg>

  <svg class="photo" style="left:6px;top:376px" width="440" height="362" role="img" aria-label="Photo of two stainless steel auger hopper screw feeders with inclined auger tubes on castor wheels">
    <defs><linearGradient id="steelA" x1="0" y1="0" x2="1" y2="1">
      <stop offset="0" stop-color="#dfe2e5"/><stop offset=".5" stop-color="#a3a8ad"/><stop offset="1" stop-color="#7e8388"/>
    </linearGradient></defs>
    <rect x="0" y="0" width="440" height="362" rx="8" fill="url(#steelA)" opacity=".8"/>
  </svg>

  <svg class="photo" style="left:240px;top:392px" width="276" height="102" role="img" aria-label="Spices and ground ingredients on white">
    <ellipse cx="138" cy="51" rx="137" ry="50" fill="#fbf6ee" stroke="#000" stroke-width="2"/>
    <ellipse cx="138" cy="51" rx="70" ry="26" fill="#e6cfa6" opacity=".6"/>
  </svg>

  <table class="spec spec--auger">
    <tr><td>MODEL</td><td>AH-A2</td><td>AH-A3</td><td>AH-A5</td><td>AH-A7</td><td>AH-A8</td><td>AH-A12</td></tr>
    <tr><td>FEEDING RATE</td><td>2m³/Hr</td><td>3m³/Hr</td><td>5m³/Hr</td><td>7m³/Hr</td><td>8m³/Hr</td><td>12m³/Hr</td></tr>
    <tr><td>PIPE DIAMETER</td><td>4"</td><td>4-1/2"</td><td>5-1/2"</td><td>6-1/4"</td><td>6-1/2"</td><td>8-1/2"</td></tr>
    <tr><td>HOPPER VOL.</td><td>3.5CF</td><td class="c" colspan="5">7CF</td></tr>
    <tr><td>DIMENSIONS</td><td>28.6"x24.4"x31.5"</td><td class="c" colspan="5">40" x 32" x 35"</td></tr>
    <tr><td>TOTAL WEIGHT</td><td>221LBS</td><td>287LBS</td><td>397LBS</td><td>441LBS</td><td>485LBS</td><td>596LBS</td></tr>
    <tr><td>CHARGING HEIGHT</td><td class="c" colspan="6">STANDARD 72 INCHES. (40" - 196" AVAILABLE)</td></tr>
    <tr><td>CHARGING ANGLE</td><td class="c" colspan="6">STANDARD 45° &nbsp;&nbsp;(30°-60° AVAILABLE)</td></tr>
  </table>
</section>

<section class="page page--ribbon">
  <svg class="masthead" viewBox="0 0 526 140" aria-hidden="true">
    <path d="M0 0H526V98Q330 128 0 46Z" fill="var(--black)"/>
    <path d="M0 46Q330 128 526 98V113Q330 142 0 68Z" fill="var(--brand-deep)"/>
  </svg>
  <div class="brand">Steelgate Equipment</div>

  <h1 class="title">RIBBON BLENDERS</h1>
  <p class="sizes">SIZES AVAILABLE; 2 CU FT. - 450 CU FT</p>

  <h2 class="section-head" style="left:11px">Standard Features</h2>
  <ul class="ticks" style="left:11px">
    <li>304 stainless steel construction</li>
    <li>Pre-wired control panels with;</li>
    <li class="plain">batch timer, on/off switch,</li>
    <li class="plain">emergency stop button</li>
    <li>Food grade compression shaft seals</li>
    <li>Safety sensor on lid for automatic</li>
    <li class="plain">shutoff when opened.</li>
    <li>Air actuated discharge valve</li>
    <li>1 piece hinged lid with safety grating</li>
    <li>Power options; 220v/4.80v.</li>
    <li>24' standard discharge height</li>
    <li>Castor wheels on 53cf units and smaller</li>
  </ul>

  <h2 class="section-head" style="left:385px">Options</h2>
  <ul class="ticks" style="left:385px">
    <li>Dual hinged lids available on custom</li>
    <li class="plain">orders.</li>
    <li>Knife gate style discharge available</li>
    <li class="plain">on custom orders.</li>
    <li>Air purge seals available on custom</li>
    <li class="plain">orders.</li>
    <li>316 stainless material available on</li>
    <li class="plain">custom orders.</li>
    <li>Custom height modification</li>
    <li>Liquid spray systems</li>
    <li>VFD) Variable Frequency Drives</li>
    <li>Leg extensions</li>
  </ul>

  <svg class="photo" style="left:161px;top:215px" width="209" height="217" role="img" aria-label="Stainless steel ribbon blender with control box on wheeled stand">
    <defs><linearGradient id="steel" x1="0" y1="0" x2="1" y2="1">
      <stop offset="0" stop-color="#d9dcdf"/><stop offset=".5" stop-color="#a7acb1"/><stop offset="1" stop-color="#c9cdd1"/>
    </linearGradient></defs>
    <rect x="8" y="20" width="190" height="190" rx="6" fill="url(#steel)" opacity=".85"/>
  </svg>

  <svg class="photo" style="left:11px;top:461px" width="264" height="98" role="img" aria-label="Colourful spices and peppercorns on spoons">
    <defs><linearGradient id="spice" x1="0" y1="0" x2="1" y2="0">
      <stop offset="0" stop-color="#5a4a35"/><stop offset=".35" stop-color="#c9611e"/><stop offset=".65" stop-color="#8a3a22"/><stop offset="1" stop-color="#4e5a2c"/>
    </linearGradient></defs>
    <ellipse cx="132" cy="49" rx="131" ry="48" fill="url(#spice)" stroke="#000" stroke-width="2"/>
    <ellipse cx="132" cy="49" rx="127" ry="44" fill="none" stroke="#fff" stroke-width="2"/>
  </svg>

  <table class="spec spec--ribbon">
    <tr><td>Model Size</td><td>5cf</td><td>7CF</td><td>10.5CF</td><td>17.5CF</td><td>35CF</td><td>53CF</td><td>70.5CF</td><td>106CF</td></tr>
    <tr><td>Working Liters</td><td>120L</td><td>200L</td><td>300L</td><td>500L</td><td>1000L</td><td>1500L</td><td>2000L</td><td>3000L</td></tr>
    <tr><td>Fill Capacity</td><td>5CF / 150L</td><td>9CF / 250L</td><td>13CF / 375L</td><td>22CF / 625L</td><td>44CF / 1250L</td><td>66CF / 1875L</td><td>88CF / 2500L</td><td>132CF / 3750L</td></tr>
    <tr><td>Weight</td><td>440lbs</td><td>550lbs</td><td>770lbs</td><td>1212lbs</td><td>1874lbs</td><td>2645lbs</td><td>3527lbs</td><td>5511lbs</td></tr>
    <tr><td>Motor Size</td><td>4hp</td><td>5.3hp</td><td>6.7hp</td><td>10hp</td><td>14.75hp</td><td>20hp</td><td>25hp</td><td>30hp</td></tr>
    <tr><td>Total Length</td><td>50"</td><td>53.5"</td><td>63"</td><td>72"</td><td>94"</td><td>102"</td><td>131.5"</td><td>157.5"</td></tr>
    <tr><td>Total Width</td><td>28"</td><td>34"</td><td>41.5"</td><td>45"</td><td>52"</td><td>66"</td><td>52.5"</td><td>54"</td></tr>
    <tr><td>Total Height</td><td>66"</td><td>69"</td><td>71"</td><td>82"</td><td>87"</td><td>95"</td><td>76"</td><td>110"</td></tr>
    <tr><td>Tub Length</td><td>31.5"</td><td>35.5"</td><td>41"</td><td>47"</td><td>59"</td><td>70"</td><td>75"</td><td>100"</td></tr>
    <tr><td>Tub Width</td><td>16.5"</td><td>22"</td><td>25"</td><td>27.5"</td><td>35.5"</td><td>39"</td><td>48"</td><td>48"</td></tr>
    <tr><td>Tub Height</td><td>20.5"</td><td>26"</td><td>28"</td><td>33"</td><td>41"</td><td>46"</td><td>51"</td><td>53"</td></tr>
    <tr><td>Shaft Diameter</td><td>2"</td><td>2-1/4"</td><td>2-5/8"</td><td>3"</td><td>3.5"</td><td>4"</td><td>4"</td><td>5-1/4"</td></tr>
    <tr><td>Tub Thickness</td><td>3mm</td><td>3mm</td><td>3mm</td><td>4mm</td><td>4mm</td><td>5mm</td><td>5mm</td><td>6mm</td></tr>
    <tr><td>Ribbon Thickness</td><td>6mm</td><td>8mm</td><td>8mm</td><td>8mm</td><td>10mm</td><td>12mm</td><td>12mm</td><td>14mm</td></tr>
    <tr><td>Max RPM</td><td>46 rpm</td><td>46 rpm</td><td>46 rpm</td><td>46 rpm</td><td>30 rpm</td><td>31 rpm</td><td>32 rpm</td><td>33 rpm</td></tr>
  </table>

  <svg class="photo" style="left:0;top:560px" width="526" height="183" viewBox="0 0 526 183" role="img" aria-label="Photo of an open ribbon blender with loading auger in a warehouse">
    <defs><linearGradient id="shop" x1="0" y1="0" x2="0" y2="1">
      <stop offset="0" stop-color="#b9bcc0"/><stop offset=".6" stop-color="#8f9398"/><stop offset="1" stop-color="#6c7075"/>
    </linearGradient></defs>
    <path d="M0 75Q260 -25 526 75V183H0Z" fill="var(--brand-deep)"/>
    <path d="M0 95Q260 -5 526 95V183H0Z" fill="url(#shop)"/>
  </svg>
</section>

</body>
</html>
```